Wordpress Design Project for Bankruptcy Law Office in San Francisco

our current website: www.dorvanelilaw-example.com

we would like to re-design it for wordpress to make it faster and a bit more modern.

content should be similar to what we have there right now but also we do family law

please include logo for law office:

Law Office of Marta K. Dolvenidze

Thank you.
Updates

please see attached word document with logos that we like as an example.

we do tend to like color red.  darker red.

Please submit your design variations and logo as soon as possible.   We would like to go over them and make our decision

Reason: Please create couple of more variations of logo for your design, so we can make our decision what we like the most. Please see word doc for samples: Text: Law Office Of Marta K. Dolvenidze

Reason: final touches

Target Market(s)

bankruptcy and family law clients

Industry/Entity Type

Family Law

Requirements
Must have
• see examples of law sites
http://promo.lexorbin-example.com/testimonials

- new logo: Law Office of Marta K. Dolvenidze
- client intake form
- blog
- contact us form

Nice to have
• - map
- red color
- on the front page a nice photo of SF or a happy family

```html
<!DOCTYPE html>
<html lang="en">
<head>
<meta charset="utf-8">
<title>Law Office of Marta K. Dolvenidze</title>
<link href="https://fonts.googleapis.com/css2?family=Cinzel:wght@400&family=Oswald:wght@300&family=Rokkitt:wght@900&family=Arimo:wght@400;700&display=swap" rel="stylesheet">
<style>
:root{
  --page-bg:#e4e4e4;
  --header-top:#ec9290;
  --header-bottom:#d86a68;
  --nav:#ad3d04;
  --white:#ffffff;
  --card:#d5706c;
  --card-dark:#c45f5b;
  --footer:#df7a78;
  --note-bg:#000000;
  --link-yellow:#ffd33a;
  --sky-top:#2f9be0;
  --sky-bottom:#6ac3f0;
  --hero-band:#c2470c;
}
*{margin:0;padding:0;box-sizing:border-box}
html,body{width:1011px;height:1200px;overflow:hidden}
body{background:var(--page-bg);position:relative;font-family:"Arimo",Arial,sans-serif}
.page{position:absolute;left:97px;top:17px;width:817px;height:1159px;background:var(--white);box-shadow:0 0 8px rgba(0,0,0,.15)}
.site-header{position:absolute;left:0;top:0;width:817px;height:91px;background:linear-gradient(180deg,var(--header-top),var(--header-bottom))}
.brand-mark{position:absolute;left:21px;top:18px;width:50px;height:50px;border-radius:50%;background:var(--white)}
.brand-name{position:absolute;left:85px;top:22px;width:285px;color:var(--white);font-family:"Cinzel",serif;font-weight:400;text-align:center;line-height:1}
.brand-name .small{display:flex;align-items:center;gap:6px;font-size:16px;letter-spacing:.5px}
.brand-name .small::before,.brand-name .small::after{content:"";flex:1;height:1px;background:rgba(255,255,255,.8)}
.brand-name .large{display:block;font-size:23px;letter-spacing:.6px;margin-top:2px;padding-bottom:4px;border-bottom:1px solid rgba(255,255,255,.8);white-space:nowrap}
.phone{position:absolute;right:10px;top:60px;display:flex;align-items:center;gap:6px;color:var(--white);font-family:"Cinzel",serif;font-size:22px;line-height:1}
.phone svg{width:21px;height:21px}
.main-nav{position:absolute;left:0;top:91px;width:817px;height:37px;background:var(--nav)}
.main-nav a{position:absolute;top:9px;transform:translateX(-50%);color:var(--white);text-decoration:none;font-family:"Oswald",sans-serif;font-weight:300;font-size:14px;white-space:nowrap}
.hero{position:absolute;left:17px;top:149px;width:786px;height:70px;background:linear-gradient(180deg,var(--sky-top),var(--sky-bottom))}
.hero-band{position:absolute;left:408px;top:56px;width:378px;height:14px;background:var(--hero-band)}
.cards{position:absolute;left:16px;top:830px;width:784px;height:170px}
.card{position:absolute;top:0;width:251px;height:170px;background:linear-gradient(180deg,var(--card),var(--card-dark));border-radius:0 0 6px 6px;box-shadow:0 6px 6px -2px rgba(0,0,0,.45)}
.card-photo{position:absolute;left:18px;top:0;width:212px;height:65px;background:linear-gradient(180deg,#d9cbc0,#8c7a70)}
.card p{position:absolute;left:17px;top:70px;width:217px;font-size:9.6px;line-height:13.5px;color:var(--white);text-align:justify}
.card .more{position:absolute;right:10px;bottom:10px;font-size:10px;font-weight:700;color:var(--link-yellow);text-decoration:none}
.site-footer{position:absolute;left:0;top:1039px;width:817px;height:120px;background:linear-gradient(180deg,var(--header-top),var(--footer))}
.footer-links{position:absolute;left:19px;top:15px;font-size:10px;color:var(--white)}
.footer-links span{margin-right:12px}
.disclaimer{position:absolute;left:19px;top:43px;width:580px;font-size:10px;line-height:15px;color:var(--white)}
.badge{position:absolute;left:712px;top:24px;width:86px;height:68px;background:var(--white);box-shadow:6px 6px 0 rgba(180,80,80,.5)}
.badge-inner{position:absolute;left:10px;top:10px;width:40px;height:48px;background:#5a86c4}
.client-note{position:absolute;left:0;top:229px;width:1011px;height:635px;background:var(--note-bg);color:var(--white);font-family:"Rokkitt",serif;font-weight:900;padding:0 0 0 83px}
.client-note p{position:absolute;left:83px;font-size:44px;line-height:49px;letter-spacing:-.3px;white-space:nowrap}
.client-note p span{display:block}
.greeting{top:58px}
.message{top:157px}
.question{top:451px}
</style>
</head>
<body>
<div class="page">
  <header class="site-header">
    <span class="brand-mark"></span>
    <div class="brand-name"><span class="small">LAW OFFICE OF</span><span class="large">MARTA K. DOLVENIDZE</span></div>
    <div class="phone">
      <svg viewBox="0 0 21 21" aria-hidden="true"><rect width="21" height="21" rx="3" fill="#f4d6d5"/><path d="M6 4c1 0 2 2.5 2 3.5S6.5 9 7 10.5s2 3 3.5 3.5 2-1 3-1 3.5 1 3.5 2-1.5 2.5-3 2.5C9 17.5 3.5 12 3.5 7 3.5 5.5 5 4 6 4z" fill="#d86a68"/></svg>
      <span>415-555-0182</span>
    </div>
  </header>
  <nav class="main-nav">
    <a href="#" style="left:84px">HOME</a>
    <a href="#" style="left:183px">ABOUT US</a>
    <a href="#" style="left:311px">AREAS OF PRACTICE</a>
    <a href="#" style="left:442px">RESOURCES</a>
    <a href="#" style="left:541px">BLOG</a>
    <a href="#" style="left:617px">FAQ</a>
    <a href="#" style="left:708px">CONTACT US</a>
  </nav>
  <div class="hero" role="img" aria-label="Hero photo of a golden butterfly against a bright blue sky with clouds">
    <div class="hero-band"></div>
  </div>
  <section class="cards">
    <article class="card" style="left:0">
      <div class="card-photo" role="img" aria-label="Photo of an attorney meeting with a couple"></div>
      <p>This page is available, however, but because occasionally circumstances occur in which toil and pain can procure him some great. To take a trivial example, which of us ever undertakes laborious physical exercise, except to obtain some advantage from it.</p>
      <a class="more" href="#">read more...</a>
    </article>
    <article class="card" style="left:267px">
      <div class="card-photo" role="img" aria-label="Photo of a smiling family in a car"></div>
      <p>This page is available, however, but because occasionally circumstances occur in which toil and pain can procure him some great. To take a trivial example, which of us ever undertakes laborious physical exercise, except to obtain some advantage from it.</p>
      <a class="more" href="#">read more...</a>
    </article>
    <article class="card" style="left:533px">
      <div class="card-photo" role="img" aria-label="Photo of a happy couple at a laptop"></div>
      <p>This page is available, however, but because occasionally circumstances occur in which toil and pain can procure him some great. To take a trivial example, which of us ever undertakes laborious physical exercise, except to obtain some advantage from it.</p>
      <a class="more" href="#">read more...</a>
    </article>
  </section>
  <footer class="site-footer">
    <div class="footer-links"><span>Go to top</span>Copyright © 2010 DKLaw. All Rights Reserved. | Web Development by Webtrellis | Design by KRA</div>
    <p class="disclaimer">Disclaimer: The Law Offices of Marta K. Dolvenidze is a Debt Relief law firm as defined by 11 U.S.C. 528. We help people file for Bankruptcy Relief under the Bankruptcy Code. The information contained on this website is not to be construed as legal advice. It is not intended to solicit or form an attorney-client relationship. We do not guarantee any result and prior results do not guarantee a similar outcome. This is an attorney advertisement and this website is for informational purposes only.</p>
    <div class="badge"><div class="badge-inner"></div></div>
  </footer>
</div>
<div class="client-note">
  <p class="greeting">Hello Sir</p>
  <p class="message"><span>I think you are not checking my messages</span><span>that I am posting you. You asked me to</span><span>see the logo of “Wren Calloway”. But I am</span><span>unable to see her logo. Could you show</span><span>me that please.</span></p>
  <p class="question"><span>I am to make changes only in logo not</span><span>in template. right ?</span></p>
</div>
</body>
</html>
```